"Inkvale" printing shop

-The design must be based around the attached HPID (home page information design) called "Inkvale - HPID".

The table boxes are just for approximate placement of information – you DON'T have to box everything in and you can arrange these. All fonts used in the HPID are only examples - you can use any Google font you wish.

- Information only is in orange text. Copy to go on the design in black text. Some instructions are in the HPID. Please be creative!

-The design needs to be modern. Colours are to be consistent with their new logo or complement it. Keep it clean and simple, you don't need to use lots of colours. Use lots of white.

- images / icons for the site need to be relevant and high quality, but they must also be free images or icons. I have attached a few examples that could be used.

Width of content will be 1100 pixels when implemented as a web page. Header height (without nav bar) 150-200 pixels.

If your design is chosen the winning PSD file will have to be provided as follows…
1. Canvas size of 2000px x 2000px - 72ppi in Adobe Photoshop (CS5 compatible)
2. Width of content section is 1100px wide - centered in the canvas
3. Any button rollovers/hovers in the PSD as hidden layers.
4. All fonts used must be Google fonts.
5. You will need to supply the chosen home page plus one example page (example page as a style guide for how all other pages will look). Example page is only the header and navigational bar at the top, an empty sector in the middle with a column (190 px wide) which can be left or right aligned which means the main sector is 910 pixels wide, and then the footer at the bottom of the page

Checklist - http://pagebuildertally.example/

Examples of some websites that have great design... don't copy them please but they are similar in look to what we are after....
http://www.rookfenly.example/

Industry/Entity Type

Printing

Font styles to use
Serif
Sans Serif

Requirements
Should not have
• Drop shadows, comic sans font

```html
<!DOCTYPE html>
<html lang="en">
<head>
<meta charset="utf-8">
<title>Inkvale – Printing Shop</title>
<link href="https://fonts.googleapis.com/css2?family=Lato:ital,wght@0,300;0,400;0,700;1,400&family=Cormorant+Garamond:ital,wght@1,500&display=swap" rel="stylesheet">
<style>
:root{
  --blue:#41bdea;
  --blue-dark:#2ea9d8;
  --ink:#222;
  --text:#333;
  --muted:#999;
  --rule:#bdbdbd;
  --paper:#ffffff;
  --wash:#f4f4f4;
  --fold:#d7d7d7;
}
*{margin:0;padding:0;box-sizing:border-box}
html,body{width:751px;height:1200px;overflow:hidden}
body{position:relative;background:var(--paper);font-family:"Lato",sans-serif;color:var(--text)}
.abs{position:absolute}

/* header */
.top-links{right:77px;top:6px;font-size:8px;color:var(--blue);display:flex;gap:12px}
.top-links span.sep{color:var(--muted)}
.brand{left:77px;top:21px;display:flex;align-items:center;gap:4px;white-space:nowrap}
.brand-dot{width:30px;height:30px;border-radius:50%;background:var(--blue);flex:none}
.brand-name{font-size:16px;font-weight:700;color:var(--blue)}
.tagline{left:175px;top:20px;font-size:19.5px;font-weight:400;letter-spacing:2.6px;color:var(--ink);white-space:nowrap}
.subline{left:175px;top:49px;font-size:7.5px;font-style:italic;letter-spacing:1px;color:var(--ink);white-space:nowrap}
.contact{left:584px;top:32px;font-size:7.5px;color:var(--ink);line-height:9px}
.contact .row{display:flex;gap:7px;align-items:flex-start;margin-bottom:5px}
.contact svg{flex:none}
.dots{left:0;width:751px;height:0;border-top:1.5px dotted var(--rule)}
.main-nav{left:77px;top:97px;font-size:7.7px;color:var(--ink);display:flex;gap:5px;white-space:nowrap}
.main-nav .sep{color:#666}

/* hero */
.hero{left:0;top:120px;width:751px;height:280px;background:var(--blue)}
.hero-title{left:104px;top:74px;font-family:"Cormorant Garamond",serif;font-style:italic;font-weight:500;font-size:26px;line-height:31px;letter-spacing:1px;color:#fff}
.hero-btn{left:104px;top:175px;width:86px;height:26px;background:#fff;border-radius:3px;color:var(--blue);font-size:8.5px;font-weight:700;display:flex;align-items:center;justify-content:center;gap:5px}
.hero-art{left:433px;top:24px;width:201px;height:233px}
.hero-arrow{top:130px;width:20px;height:20px;border-radius:50%;background:#fff;display:flex;align-items:center;justify-content:center}
.hero-base{left:120px;top:398px;width:511px;height:20px;background:radial-gradient(ellipse at 50% 0,rgba(0,0,0,.28),rgba(0,0,0,0) 70%)}

/* services */
.services{left:0;top:418px;width:751px;height:457px;background:var(--wash)}
.card{width:189px;height:196px;background:var(--blue);color:#fff;text-align:center}
.card-fold{position:absolute;left:0;top:0}
.card-icon{position:absolute;left:75px;top:20px;width:38px;height:38px}
.card-title{position:absolute;left:0;right:0;top:62px;font-size:15.5px;font-weight:300}
.card-title span{border-bottom:1px solid rgba(255,255,255,.8);padding-bottom:2px}
.card-sub{position:absolute;left:0;right:0;top:95px;font-size:9.5px;font-weight:700}
.card-body{position:absolute;left:12px;right:12px;top:113px;font-size:7.2px;line-height:8.4px}
.card-btn{position:absolute;left:60px;top:160px;width:70px;height:19px;background:#fff;border-radius:3px;color:var(--blue);font-size:7.5px;font-weight:700;display:flex;align-items:center;justify-content:center;gap:4px}
.card-shade{width:189px;height:12px;background:radial-gradient(ellipse at 50% 0,rgba(0,0,0,.55),rgba(0,0,0,0) 70%)}

/* quote + form */
.contact-band{left:0;top:875px;width:751px;height:236px;background:#f3f3f3}
.h-section{font-size:14px;font-weight:400;color:var(--ink)}
.quote-copy{left:77px;top:929px;width:252px;font-size:10.2px;line-height:13px;color:var(--ink)}
.socials{left:77px;top:1056px;display:flex;gap:13px}
.socials span{width:30px;height:30px;border-radius:50%;background:var(--blue)}
.field{background:#fff;border:1px solid var(--blue);font-size:7.5px;color:var(--muted);padding:6px 5px}
.submit{left:384px;top:1065px;width:69px;height:19px;border-radius:3px;background:var(--blue);color:#fff;font-size:7.5px;font-weight:700;display:flex;align-items:center;justify-content:center}

/* footer */
.foot-bar{left:0;top:1111px;width:751px;height:41px;background:var(--blue);display:flex;align-items:center;justify-content:center;gap:3px;font-size:6.4px;color:#fff;white-space:nowrap}
.copyright{left:0;top:1170px;width:751px;text-align:center;font-size:7.2px;color:var(--blue)}
</style>
</head>
<body>

<!-- header -->
<nav class="abs top-links"><span>Home</span><span class="sep">|</span><span>About</span><span class="sep">|</span><span>Free Quote</span><span class="sep">|</span><span>Contact</span></nav>
<div class="abs brand"><span class="brand-dot"></span><span class="brand-name">Inkvale</span></div>
<div class="abs tagline">Duplication is our vocation</div>
<div class="abs subline">Professional photocopying - digital &amp; film processing, design and printing</div>
<div class="abs contact">
  <div class="row">
    <svg width="8" height="8" viewBox="0 0 24 24"><path fill="#222" d="M6.6 10.8a15 15 0 0 0 6.6 6.6l2.2-2.2c.3-.3.7-.4 1-.2 1.1.4 2.3.6 3.6.6.6 0 1 .4 1 1V20c0 .6-.4 1-1 1A17 17 0 0 1 3 4c0-.6.4-1 1-1h3.5c.6 0 1 .4 1 1 0 1.3.2 2.5.6 3.6.1.3 0 .7-.2 1z"/></svg>
    <span>07 555 0148,</span>
  </div>
  <div class="row">
    <svg width="8" height="10" viewBox="0 0 24 30"><path fill="#222" d="M12 0C5.4 0 0 5.3 0 11.8 0 20.6 12 30 12 30s12-9.4 12-18.2C24 5.3 18.6 0 12 0zm0 16a4.5 4.5 0 1 1 0-9 4.5 4.5 0 0 1 0 9z"/></svg>
    <span>3/58 Kelmer Road<br>Ashby - Tauranga</span>
  </div>
</div>
<div class="abs dots" style="top:82px"></div>
<nav class="abs main-nav">
  <span>Photocopying</span><span class="sep">|</span><span>Printing</span><span class="sep">|</span><span>Laminating</span><span class="sep">|</span><span>Business cards</span><span class="sep">|</span><span>Typing Services</span><span class="sep">|</span><span>Film Processing</span><span class="sep">|</span><span>Photo Printing</span><span class="sep">|</span><span>Passport Photos</span><span class="sep">|</span><span>Image Restoration</span><span class="sep">|</span><span>Printer Supplies</span>
</nav>
<div class="abs dots" style="top:119px"></div>

<!-- hero -->
<section class="abs hero">
  <h1 class="abs hero-title">Digital Printing Laminating<br>Photocopying Services<br>Throughout Tauranga</h1>
  <div class="abs hero-btn">LEARN MORE <svg width="5" height="8" viewBox="0 0 5 8"><path d="M1 1l3 3-3 3" stroke="#41bdea" stroke-width="1.5" fill="none"/></svg></div>
  <div class="abs hero-art" role="img" aria-label="Illustration of a sunflower half turning into a halftone dot pattern, circled by a green arrow">
    <svg width="201" height="233" viewBox="0 0 201 233">
      <defs><radialGradient id="bloom" cx="50%" cy="55%" r="50%"><stop offset="0" stop-color="#f7d21a"/><stop offset="1" stop-color="#e8b90f"/></radialGradient></defs>
      <circle cx="105" cy="125" r="95" fill="url(#bloom)"/>
    </svg>
  </div>
  <div class="abs hero-arrow" style="left:16px"><svg width="6" height="8" viewBox="0 0 6 8"><path d="M4.5 1L1.5 4l3 3" stroke="#41bdea" stroke-width="1.8" fill="none"/></svg></div>
  <div class="abs hero-arrow" style="left:715px"><svg width="6" height="8" viewBox="0 0 6 8"><path d="M1.5 1l3 3-3 3" stroke="#41bdea" stroke-width="1.8" fill="none"/></svg></div>
</section>

<!-- services -->
<section class="abs services"></section>
<div class="abs hero-base"></div>

<!-- row 1 -->
<article class="abs card" style="left:77px;top:444px">
  <svg class="card-fold" width="60" height="66" viewBox="0 0 60 66"><path d="M0 0H52C44 6 42 18 48 26L0 66Z" fill="#d7d7d7"/><path d="M0 66L48 26C36 30 20 44 0 66Z" fill="#f2f2f2"/></svg>
  <svg class="card-icon" viewBox="0 0 38 38"><circle cx="19" cy="19" r="19" fill="#fff"/><path d="M8 18l11-6 11 6-11 6z" fill="#41bdea"/><path d="M8 21l11 6 11-6M8 24l11 6 11-6" stroke="#41bdea" stroke-width="1.8" fill="none"/></svg>
  <h2 class="card-title"><span>Photocopying</span></h2>
  <h3 class="card-sub">Cost effective photocopying</h3>
  <p class="card-body">No matter the quantity of photocopies you need or the size of your copy - you can rely on us to provide a top quality service!</p>
  <div class="card-btn">READ MORE <svg width="4" height="7" viewBox="0 0 4 7"><path d="M.7.7l2.6 2.8L.7 6.3" stroke="#41bdea" stroke-width="1.3" fill="none"/></svg></div>
</article>
<article class="abs card" style="left:282px;top:444px">
  <svg class="card-fold" width="60" height="66" viewBox="0 0 60 66"><path d="M0 0H52C44 6 42 18 48 26L0 66Z" fill="#d7d7d7"/><path d="M0 66L48 26C36 30 20 44 0 66Z" fill="#f2f2f2"/></svg>
  <svg class="card-icon" viewBox="0 0 38 38"><circle cx="19" cy="19" r="19" fill="#fff"/><rect x="10" y="11" width="16" height="8" rx="3" fill="#41bdea"/><rect x="17" y="17" width="10" height="12" rx="2" fill="#41bdea"/><circle cx="14" cy="15" r="2" fill="#fff"/></svg>
  <h2 class="card-title"><span>Laminating &amp; Binding</span></h2>
  <h3 class="card-sub">Laminating and binding</h3>
  <p class="card-body">Create a professional image for your documents or books. Lamination and binding also keeps your documents well protected!</p>
  <div class="card-btn">READ MORE <svg width="4" height="7" viewBox="0 0 4 7"><path d="M.7.7l2.6 2.8L.7 6.3" stroke="#41bdea" stroke-width="1.3" fill="none"/></svg></div>
</article>
<article class="abs card" style="left:485px;top:444px">
  <svg class="card-fold" width="60" height="66" viewBox="0 0 60 66"><path d="M0 0H52C44 6 42 18 48 26L0 66Z" fill="#d7d7d7"/><path d="M0 66L48 26C36 30 20 44 0 66Z" fill="#f2f2f2"/></svg>
  <svg class="card-icon" viewBox="0 0 38 38"><rect x="11" y="3" width="16" height="10" fill="#fff"/><rect x="3" y="12" width="32" height="16" rx="2" fill="#fff"/><rect x="10" y="22" width="18" height="13" fill="#fff" stroke="#41bdea" stroke-width="1.2"/><path d="M13 27h12M13 30h12" stroke="#41bdea"/></svg>
  <h2 class="card-title"><span>Digital Printing</span></h2>
  <h3 class="card-sub">All digital format printing</h3>
  <p class="card-body">Either email us your file or bring it into the store and we can get you the print you need. All prints are to the highest quality.</p>
  <div class="card-btn">READ MORE <svg width="4" height="7" viewBox="0 0 4 7"><path d="M.7.7l2.6 2.8L.7 6.3" stroke="#41bdea" stroke-width="1.3" fill="none"/></svg></div>
</article>
<div class="abs card-shade" style="left:77px;top:640px"></div>
<div class="abs card-shade" style="left:282px;top:640px"></div>
<div class="abs card-shade" style="left:485px;top:640px"></div>

<!-- row 2 -->
<article class="abs card" style="left:77px;top:656px">
  <svg class="card-fold" width="60" height="66" viewBox="0 0 60 66"><path d="M0 0H52C44 6 42 18 48 26L0 66Z" fill="#d7d7d7"/><path d="M0 66L48 26C36 30 20 44 0 66Z" fill="#f2f2f2"/></svg>
  <svg class="card-icon" viewBox="0 0 38 38"><circle cx="19" cy="19" r="17" fill="#fff"/><circle cx="19" cy="11" r="3.5" fill="#41bdea"/><circle cx="19" cy="27" r="3.5" fill="#41bdea"/><circle cx="11" cy="19" r="3.5" fill="#41bdea"/><circle cx="27" cy="19" r="3.5" fill="#41bdea"/><path d="M26 36h12" stroke="#fff" stroke-width="2"/></svg>
  <h2 class="card-title"><span>Film Processing</span></h2>
  <h3 class="card-sub">Film photo processing</h3>
  <p class="card-body">Bring in your film to the store and we will work with you to get the best quality print for your purpose and needs. We work with it all!</p>
  <div class="card-btn">READ MORE <svg width="4" height="7" viewBox="0 0 4 7"><path d="M.7.7l2.6 2.8L.7 6.3" stroke="#41bdea" stroke-width="1.3" fill="none"/></svg></div>
</article>
<article class="abs card" style="left:282px;top:656px">
  <svg class="card-fold" width="60" height="66" viewBox="0 0 60 66"><path d="M0 0H52C44 6 42 18 48 26L0 66Z" fill="#d7d7d7"/><path d="M0 66L48 26C36 30 20 44 0 66Z" fill="#f2f2f2"/></svg>
  <svg class="card-icon" viewBox="0 0 38 38" style="left:70px;width:48px"><rect x="1" y="6" width="36" height="26" rx="2" fill="#fff"/><rect x="5" y="11" width="11" height="15" fill="#41bdea"/><path d="M19 13h14M19 18h14M19 23h14M5 28h28" stroke="#41bdea" stroke-width="2"/></svg>
  <h2 class="card-title"><span>Business Cards</span></h2>
  <h3 class="card-sub">Personal desktop publishing</h3>
  <p class="card-body">From personalised brochures, posters and birth-day and special occasion cards to top quality, cheap business cards - you get it all!</p>
  <div class="card-btn">READ MORE <svg width="4" height="7" viewBox="0 0 4 7"><path d="M.7.7l2.6 2.8L.7 6.3" stroke="#41bdea" stroke-width="1.3" fill="none"/></svg></div>
</article>
<article class="abs card" style="left:485px;top:656px">
  <svg class="card-fold" width="60" height="66" viewBox="0 0 60 66"><path d="M0 0H52C44 6 42 18 48 26L0 66Z" fill="#d7d7d7"/><path d="M0 66L48 26C36 30 20 44 0 66Z" fill="#f2f2f2"/></svg>
  <svg class="card-icon" viewBox="0 0 38 38"><rect x="10" y="2" width="18" height="9" fill="#fff"/><rect x="3" y="12" width="32" height="15" rx="5" fill="#fff"/><rect x="9" y="24" width="20" height="12" rx="2" fill="#fff" stroke="#41bdea" stroke-width="1.2"/><path d="M3 19h32" stroke="#41bdea" stroke-width="1.5"/></svg>
  <h2 class="card-title"><span>Photo Printing</span></h2>
  <h3 class="card-sub">Quality digital photo prints</h3>
  <p class="card-body">Get your photo printed to your requirements - either from a file or from your digital camera. With a wide range of options you can get the print you want.</p>
  <div class="card-btn">READ MORE <svg width="4" height="7" viewBox="0 0 4 7"><path d="M.7.7l2.6 2.8L.7 6.3" stroke="#41bdea" stroke-width="1.3" fill="none"/></svg></div>
</article>
<div class="abs card-shade" style="left:77px;top:851px"></div>
<div class="abs card-shade" style="left:282px;top:851px"></div>
<div class="abs card-shade" style="left:485px;top:851px"></div>

<!-- quote and form -->
<section class="abs contact-band"></section>
<h2 class="abs h-section" style="left:77px;top:901px">Get a free quote</h2>
<p class="abs quote-copy">...or talk to our team about your requirements. Please fill out the form below and we will contact you within a day. You can now upload and send us your file for a free quote</p>
<h2 class="abs h-section" style="left:77px;top:1025px">Follow Us!</h2>
<div class="abs socials"><span></span><span></span><span></span><span></span><span></span><span></span></div>

<h2 class="abs h-section" style="left:384px;top:901px">Equire Form</h2>
<div class="abs field" style="left:384px;top:932px;width:140px;height:22px">First name</div>
<div class="abs field" style="left:534px;top:932px;width:139px;height:22px">Last name</div>
<div class="abs field" style="left:384px;top:962px;width:140px;height:22px">Number</div>
<div class="abs field" style="left:534px;top:962px;width:139px;height:22px">Email</div>
<div class="abs field" style="left:384px;top:992px;width:289px;height:64px">Message</div>
<div class="abs submit">SUBMIT</div>

<!-- footer -->
<footer class="abs foot-bar">
  <span>Home</span>|<span>About</span>|<span>Photocopying</span>|<span>Printing</span>|<span>Laminating</span>|<span>Business cards</span>|<span>Typing Services</span>|<span>Film Processing</span>|<span>Photo Printing</span>|<span>Passport Photos</span>|<span>Image Restoration</span>|<span>Printer Supplies</span>|<span>Free Quote</span>|<span>Contact</span>
</footer>
<p class="abs copyright">© Copyright 2015 Inkvale Printing Shop . All Rights Reserved.</p>

</body>
</html>
```